Structural Engineering Business Card

Brookvane Drafting does residential house plans for clients in Central Florida. Would like simple but elegant business card that is appropriate for a house plan engineering company. Prefer black business card with black/white them but open to other shades of blue. I uploaded a sample card that I came across that looked good but please come up with your own creative designs.

Contact Information for Business Card

Name, Title, Phone, Email, Address, website

```html
<!DOCTYPE html>
<html lang="en">
<head>
<meta charset="utf-8">
<title>Brookvane Drafting – Business Card</title>
<link href="https://fonts.googleapis.com/css2?family=Arimo:wght@400;700&display=swap" rel="stylesheet">
<style>
  :root {
    --canvas: #e4e4e4;
    --card: #1b1b1b;
    --ink: #ffffff;
    --ink-soft: #d6d6d6;
    --rule: #8a8a8a;
  }
  * { box-sizing: border-box; margin: 0; padding: 0; }
  html, body {
    width: 1200px; height: 800px; overflow: hidden;
    background: var(--canvas);
    font-family: "Arimo", Arial, sans-serif;
  }
  .sheet {
    width: 1200px; height: 800px;
    display: flex; align-items: center; justify-content: center; gap: 44px;
  }
  .card {
    position: relative;
    width: 540px; height: 309px;
    background: var(--card);
    border-radius: 22px;
    color: var(--ink);
    box-shadow: 0 10px 28px rgba(0,0,0,.22);
  }
  .wordmark {
    font-weight: 700;
    text-transform: uppercase;
    color: var(--ink);
    display: flex; align-items: center; gap: 10px;
    line-height: 1;
  }
  .wordmark .mark-square { width: 14px; height: 14px; background: var(--ink); flex: none; }

  /* Front: contact side */
  .card--front .wordmark {
    position: absolute; right: 34px; top: 46px;
    font-size: 22px; letter-spacing: .5px;
  }
  .card--front .divider {
    position: absolute; left: 30px; right: 30px; top: 158px;
    height: 1px; background: var(--rule);
  }
  .person { position: absolute; left: 34px; bottom: 160px; }
  .person__name { font-size: 19px; font-weight: 700; letter-spacing: .5px; text-transform: uppercase; }
  .person__title { font-size: 13px; color: var(--ink-soft); margin-top: 4px; }

  .contact { position: absolute; left: 34px; top: 174px; list-style: none; }
  .contact li { display: flex; align-items: center; gap: 9px; font-size: 13px; line-height: 20px; color: var(--ink-soft); }
  .contact svg { width: 12px; height: 12px; flex: none; }

  .address { position: absolute; right: 34px; top: 174px; text-align: right; font-size: 13px; line-height: 20px; color: var(--ink-soft); font-style: normal; }

  /* Back: brand side */
  .card--back { display: flex; align-items: center; justify-content: center; }
  .card--back .wordmark { font-size: 34px; letter-spacing: 1px; }
  .card--back .wordmark .mark-square { width: 22px; height: 22px; }
</style>
</head>
<body>
<main class="sheet">

  <section class="card card--front" aria-label="Business card, contact side">
    <div class="wordmark"><span class="mark-square"></span>Brookvane Drafting</div>

    <div class="person">
      <p class="person__name">Daniel Whitcomb</p>
      <p class="person__title">Managing Director</p>
    </div>

    <div class="divider"></div>

    <ul class="contact">
      <li>
        <svg viewBox="0 0 12 12" aria-hidden="true"><path d="M2.5 1 L4.3 1 L5 3.4 L3.9 4.4 C4.5 5.8 5.9 7.3 7.5 8 L8.5 7 L11 7.7 L11 9.5 C11 10.3 10.3 11 9.5 11 C5 11 1 7 1 2.5 C1 1.7 1.7 1 2.5 1 Z" fill="#fff"/></svg>
        407-555-0182
      </li>
      <li>
        <svg viewBox="0 0 12 12" aria-hidden="true"><rect x="1.5" y="1.5" width="9" height="9" fill="none" stroke="#fff" stroke-width="1.2"/></svg>
        407-555-0147
      </li>
      <li>
        <svg viewBox="0 0 12 12" aria-hidden="true"><rect x="1" y="1" width="10" height="10" fill="#fff"/><path d="M3 6.2 L5.2 8.2 L9 3.8" fill="none" stroke="#1b1b1b" stroke-width="1.5"/></svg>
        info@brookvanedrafting.com
      </li>
    </ul>

    <address class="address">
      1240 Cypress Hollow Road<br>
      Sanford, Florida 32771<br>
      www.brookvanedrafting.com
    </address>
  </section>

  <section class="card card--back" aria-label="Business card, brand side">
    <div class="wordmark"><span class="mark-square"></span>Brookvane Drafting</div>
  </section>

</main>
</body>
</html>
```